Marwick Law Letterhead

We need a new letterhead design for a Law Firm. The address for the law firm is 1475 Calloway Street, Suite 210, Houston, Texas 77041. Phone Number: 832-361-9027; Fax Number: 832-614-7359. The logo is uploaded to the project.

```html
<!DOCTYPE html>
<html lang="en">
<head>
<meta charset="utf-8">
<title>Marwick Law Letterhead</title>
<link href="https://fonts.googleapis.com/css2?family=Montserrat:wght@400;500;600&display=swap" rel="stylesheet">
<style>
  :root {
    --backdrop: #e9eaec;
    --paper: #ffffff;
    --navy: #1f2f5c;
    --red: #e0202c;
    --red-dark: #7a0d14;
    --ink: #2b2b2b;
    --muted: #444;
  }
  * { margin: 0; padding: 0; box-sizing: border-box; }
  html, body {
    width: 1200px; height: 960px; overflow: hidden;
    background: var(--backdrop);
    font-family: "Montserrat", sans-serif;
  }
  .letterhead {
    position: absolute; left: 275px; top: 20px;
    width: 650px; height: 920px;
    background: var(--paper);
    box-shadow: 0 4px 18px rgba(0,0,0,0.12);
    padding: 0 58px;
  }
  .brand {
    position: absolute; left: 58px; top: 62px;
    display: flex; align-items: center; gap: 12px;
  }
  .brand-mark { width: 30px; height: 30px; background: var(--navy); }
  .brand-name {
    font-size: 24px; font-weight: 600; color: var(--navy);
    letter-spacing: 0.5px;
  }
  .contact {
    position: absolute; right: 58px; top: 40px;
    padding-left: 12px;
    border-left: 1px solid var(--red);
    height: 112px;
    font-size: 10.5px; line-height: 1.45; color: var(--ink);
  }
  .contact-line { display: flex; align-items: center; gap: 6px; }
  .contact-line svg { width: 10px; height: 10px; flex: none; }
  .contact-address { margin-bottom: 3px; }
  .header-rule {
    position: absolute; left: 58px; right: 58px; top: 152px;
    height: 1px; background: var(--red);
  }
  .header-bar {
    position: absolute; left: 300px; top: 149px;
    width: 170px; height: 7px;
    background: linear-gradient(90deg, var(--red), var(--red-dark));
  }
  .recipient {
    position: absolute; left: 58px; top: 190px;
    font-size: 11px; line-height: 1.5; color: var(--ink);
  }
  .letter-body {
    position: absolute; left: 58px; right: 58px; top: 262px;
    font-size: 10.5px; line-height: 1.6; color: var(--muted);
  }
  .letter-body p { margin-bottom: 16px; }
  .closing {
    position: absolute; left: 58px; top: 790px;
    font-size: 12px; color: var(--ink);
  }
  .signature {
    margin-top: 10px; width: 120px; height: 38px;
    background: linear-gradient(90deg, rgba(30,30,30,0.18), rgba(30,30,30,0.04));
    border-radius: 4px;
  }
</style>
</head>
<body>
  <main class="letterhead">
    <div class="brand">
      <span class="brand-mark"></span>
      <span class="brand-name">Marwick Law</span>
    </div>

    <address class="contact" style="font-style:normal">
      <div class="contact-address">1475 Calloway Street,<br>Suite 210, Houston,<br>Texas 77041</div>
      <div class="contact-line">
        <svg viewBox="0 0 10 10" aria-hidden="true"><path d="M2 1l2 2-1 1.2c.6 1.2 1.6 2.2 2.8 2.8L7 6l2 2-1.2 1.2C4.5 9 1 5.5.8 2.2z" fill="#e0202c"/></svg>
        832-361-9027
      </div>
      <div class="contact-line">
        <svg viewBox="0 0 10 10" aria-hidden="true"><rect x="2.5" y="0.5" width="5" height="3" fill="#e0202c"/><rect x="0.5" y="3.5" width="9" height="4" rx="1" fill="#e0202c"/><rect x="2.5" y="6.5" width="5" height="3" fill="#e0202c"/></svg>
        832-614-7359
      </div>
    </address>

    <div class="header-rule"></div>
    <div class="header-bar"></div>

    <div class="recipient">
      Mr/s<br>First Name and Last Name<br>Company Name<br>Address
    </div>

    <section class="letter-body">
      <p>Lorem ipsum dolor sit amet,consectetur adipiscing sed do eiusmod tempor incididunt laboreet dolore magna aliqua.Ut enim ad minim.veniam, quis nostrud exercitation ullamco laboris nisi ut aliquip exea commodo consequat.Lorem ipsum dolor sit amet,consectetur adipiscing sed do eiusmod tempor incididunt.labore et dolore magna aliqua. Ut enim</p>
      <p>Lorem ipsum dolor sit amet, consectetur adipiscing sed do eiusmod tempor incididunt labore et dolore magna aliqua. Ut enim ad minim veniam, quis nostrud exercitation ullamco laboris nisi ut aliquip exea commodo consequat.Duis aute irure dolor in reprehenderit in voluptate velit esse cillum irure dolor in reprehenderit in voluptate velit esse irure</p>
      <p>Lorem ipsum dolor sit amet, consectetur adipiscing sed do eiusmod tempor incididunt in voluptate velit esse cillum dolore eu fugiat nulla pariatur. Excepteur sint occaecat cupidatat non proident, sunt in culpa qui officia deserunt mollit,</p>
      <p>Lorem ipsum dolor sit amet, consectetur adipiscing sed do eiusmod tempor incididunt labore et dolore magna aliqua. Ut enim Lorem ipsum dolor sit amet, consectetur adipiscing sed do eiusmod tempor incididunt labore et dolore magna aliqua. Ut enim Lorem ipsum aliqua.ipsum</p>
      <p>Lorem ipsum dolor sit amet, consectetur adipiscing sed do eiusmod tempor incididunt labore et dolore magna aliqua. Ut enim ad minim veniam, quis nostrud exercitation ullamco laboris nisi ut aliquip exea commodo consequat.Duis aute irure dolor in reprehenderit in voluptate velit esse cillum irure dolor in reprehenderit in voluptate velit esse irure</p>
      <p>Lorem ipsum dolor sit amet, consectetur adipiscing sed do eiusmod tempor incididunt labore et dolore magna aliqua. Ut enim ad minim veniam, quis nostrud exercitation ullamco laboris nisi ut aliquip exea commodo consequat.Duis aute irure dolor in reprehenderit in voluptate velit esse cillum irure dolor in reprehenderit in voluptate velit esse irure</p>
    </section>

    <div class="closing">
      Regards
      <div class="signature" role="img" aria-label="Handwritten signature"></div>
    </div>
  </main>
</body>
</html>
```